Upmarket Dessert Lounge needs a Business Card Design

We are an upmarket dessert lounge needing a business card to match our image.

We want something that is simple yet beautiful, feminine, classy, sophisticated and elegant. We want it to stand out and don't mind if it is bold.

The design should include our logo and colours of red or maroon with gold highlights. We don't mind if black is used.

Marlow & Quince

Target Market(s)

For those who like to indulge or treat themselves and give in to their temptations on good quality desserts.

Industry/Entity Type

Business

Requirements
Must have
• Must include our logo and our name

Marlow & Quince

M & Q

```html
<!DOCTYPE html>
<html lang="en">
<head>
<meta charset="utf-8">
<title>Marlow &amp; Quince — Business Card</title>
<link href="https://fonts.googleapis.com/css2?family=Cormorant+Garamond:wght@500&family=Tinos:ital,wght@0,400;0,700;1,400&display=swap" rel="stylesheet">
<style>
  :root {
    --backdrop: #3a3a3a;
    --card-red: #7e1418;
    --card-red-deep: #6c1014;
    --gold: #f4dba4;
    --radius: 22px;
  }
  * { margin: 0; padding: 0; box-sizing: border-box; }
  html, body { width: 1200px; height: 900px; overflow: hidden; }
  body {
    background: var(--backdrop);
    font-family: "Tinos", "Times New Roman", serif;
    color: var(--gold);
    position: relative;
  }
  .card {
    position: absolute;
    top: 308px;
    width: 513px;
    height: 285px;
    border-radius: var(--radius);
    overflow: hidden;
  }
  .card--front { left: 73px; }
  .card--back { left: 615px; }
  .card__pattern {
    position: absolute; inset: 0;
    background: radial-gradient(ellipse at center, var(--card-red) 0%, var(--card-red-deep) 100%);
  }
  .card__content { position: absolute; inset: 0; }

  .brand-name {
    position: absolute;
    left: 0; right: 0; top: 118px;
    text-align: center;
    font-family: "Cormorant Garamond", Georgia, serif;
    font-weight: 500;
    font-size: 34px;
    letter-spacing: 1px;
    text-transform: uppercase;
  }
  .tagline {
    position: absolute;
    left: 0; right: 0; top: 247px;
    text-align: center;
    font-size: 11px;
    font-weight: 700;
    letter-spacing: 5.5px;
    text-transform: uppercase;
  }

  .owner {
    position: absolute;
    left: 0; right: 0; top: 26px;
    text-align: center;
    font-size: 13px;
  }
  .owner__name { font-weight: 700; }
  .owner__role { font-style: italic; }
  .monogram {
    position: absolute;
    left: 0; right: 0; top: 100px;
    text-align: center;
    font-family: "Cormorant Garamond", Georgia, serif;
    font-weight: 500;
    font-size: 66px;
    line-height: 1;
  }
  .contact {
    position: absolute;
    top: 236px;
    font-size: 12.5px;
    line-height: 16px;
  }
  .contact--place { right: 283px; text-align: right; }
  .contact--online { left: 240px; }
</style>
</head>
<body>
  <section class="card card--front">
    <div class="card__pattern" role="img" aria-label="Deep red card with a faint tone-on-tone floral damask pattern"></div>
    <div class="card__content">
      <h1 class="brand-name">Marlow &amp; Quince</h1>
      <p class="tagline">Upmarket Dessert Lounge</p>
    </div>
  </section>

  <section class="card card--back">
    <div class="card__pattern" role="img" aria-label="Deep red card with a faint tone-on-tone floral damask pattern"></div>
    <div class="card__content">
      <p class="owner"><span class="owner__name">CLARA WHITFIELD</span> <span class="owner__role">— founder and owner</span></p>
      <p class="monogram">M&amp;Q</p>
      <p class="contact contact--place">Larkfield, South Australia<br>555 010 20 30</p>
      <p class="contact contact--online">info@marlow-quince.com | www.marlow-quince.com<br>www.pagebook.com/Marlow.Quince</p>
    </div>
  </section>
</body>
</html>
```